Homemaking training schools needs a Business Card design

Designer, Hello!

No special requirements, good-looking enough.
--------------------------------------------------------------------------

Name: Marcus Dole
Chairman
Tel: 0574-71948263
Mobile: 13857420916
Email: kelvora@mailnest.example
Web: www.prt2019.example
Add: No.258, LanpingJie, BeiyuanQu, Ningbo, Zhejiang

LOGO
Ningbo PRT Homemaking Training School

Target Market(s)

pregnant women, mothers, infants, the elderly and families, including cleaning, cooking, nursing training.

Industry/Entity Type

Business

Contact Information for Business Card

Name: Marcus Dole
Chairman
Tel: 0574-71948263
Mobile: 13857420916
Email: kelvora@mailnest.example
Web: www.prt2019.example

LOGO

Font styles to use
Serif
Sans Serif
Decorative

Requirements
Nice to have
• Feels: clean, specifications, safety, comfort, warmth and happiness.

```html
<!DOCTYPE html>
<html lang="en">
<head>
<meta charset="utf-8">
<title>PengRuiTang Business Card – Marcus Dole</title>
<link rel="stylesheet" href="https://fonts.googleapis.com/css2?family=Comfortaa:wght@700&family=Open+Sans:wght@400&family=Yellowtail&family=Josefin+Sans:wght@700&display=swap">
<style>
  :root {
    --card-bg: #0d1e2b;
    --brand-blue: #1b75bc;
    --mint: #7ecfae;
    --rust: #c7553a;
    --rule-grey: #3a4652;
  }
  html, body {
    margin: 0;
    padding: 0;
    width: 1200px;
    height: 704px;
    overflow: hidden;
    background: var(--card-bg);
  }
  .card {
    position: relative;
    width: 1200px;
    height: 704px;
    background: var(--card-bg);
    overflow: hidden;
  }
  .monogram {
    position: absolute;
    top: 62px;
    left: 0;
    width: 1200px;
    margin: 0;
    text-align: center;
    font-family: "Comfortaa", sans-serif;
    font-weight: 700;
    font-size: 34px;
    line-height: 40px;
    letter-spacing: 6px;
    color: var(--mint);
  }
  .brand-name {
    position: absolute;
    top: 306px;
    left: 0;
    width: 1200px;
    margin: 0;
    text-align: center;
    font-family: "Comfortaa", sans-serif;
    font-weight: 700;
    font-size: 98px;
    line-height: 110px;
    letter-spacing: 9px;
    text-indent: 9px;
    color: var(--brand-blue);
  }
  .tagline {
    position: absolute;
    top: 400px;
    left: 0;
    width: 1200px;
    margin: 0;
    text-align: center;
    font-family: "Open Sans", sans-serif;
    font-weight: 400;
    font-size: 38px;
    line-height: 50px;
    letter-spacing: -0.5px;
    color: var(--brand-blue);
  }
  .rule {
    position: absolute;
    top: 425px;
    height: 2px;
    width: 162px;
    background: var(--rule-grey);
  }
  .rule--left { left: 226px; }
  .rule--right { left: 813px; }
  .person-name {
    position: absolute;
    left: 208px;
    top: 500px;
    margin: 0;
    font-family: "Yellowtail", cursive;
    font-size: 100px;
    line-height: 120px;
    font-weight: 400;
    color: var(--rust);
    white-space: nowrap;
  }
  .person-title {
    position: absolute;
    left: 281px;
    top: 618px;
    margin: 0;
    font-family: "Josefin Sans", sans-serif;
    font-weight: 700;
    font-size: 27px;
    line-height: 30px;
    letter-spacing: 1px;
    text-transform: uppercase;
    color: var(--mint);
  }
  .contact {
    position: absolute;
    left: 772px;
    top: 548px;
    margin: 0;
    font-family: "Josefin Sans", sans-serif;
    font-weight: 700;
    font-size: 17px;
    line-height: 20.3px;
    letter-spacing: 1px;
    text-transform: uppercase;
    color: var(--rust);
    font-style: normal;
  }
  .contact-line { margin: 0; white-space: nowrap; }
  .contact-address {
    margin-top: 20px;
    white-space: nowrap;
  }
  .contact-address .address-cont {
    display: block;
    padding-left: 56px;
  }
</style>
</head>
<body>
  <main class="card">
    <p class="monogram">PRT</p>

    <h1 class="brand-name">PengRuiTang</h1>
    <span class="rule rule--left" aria-hidden="true"></span>
    <p class="tagline">Training &amp; Services</p>
    <span class="rule rule--right" aria-hidden="true"></span>

    <h2 class="person-name">Marcus Dole</h2>
    <p class="person-title">Chairman</p>

    <address class="contact">
      <p class="contact-line">Tel: 0574-71948263</p>
      <p class="contact-line">Mobile: 13857420916</p>
      <p class="contact-line">Email: kelvora@mailnest.example</p>
      <p class="contact-line">Web: www.prt2019.example</p>
      <p class="contact-line contact-address">Add: No.258, LanpingJie, BeiyuanQu,<span class="address-cont">Ningbo, Zhejiang</span></p>
    </address>
  </main>
</body>
</html>
```